Private Investigation Business Card Design

I need a business card for a new private investigation company named Brisk Inquiries. I perform mainly surveillance jobs, vehicle repossessions, document serves etc. The final design should aim for a professional look. The logo has a magnifying glass with stick man arms and legs and is in a running action to show the "Brisk" aspect of the name. If the colour scheme could remain the same as the website www.briskinquiries-demo.com.au with silvers,blacks and a couple electric blue highlights.
Industry/Entity Type
Business
Contact Information for Business Card
Morgan Kellaway
Brisk Inquiries
0487316204
PO Box 58, Carnwell NSW 2291
info@briskinquiries-demo.com.au
www.briskinquiries-demo.com.au
Look and feel

```html
<!DOCTYPE html>
<html lang="en">
<head>
<meta charset="utf-8">
<title>Brisk Inquiries – Business Card</title>
<link href="https://fonts.googleapis.com/css2?family=Play:wght@400;700&display=swap" rel="stylesheet">
<style>
  :root {
    --backdrop: #3a3a3a;
    --card-white: #f7f7f7;
    --silver-dark: #8f8f91;
    --silver-mid: #b5b5b7;
    --silver-light: #d9d9da;
    --ink: #2b2b2b;
    --ink-soft: #4a4a4a;
    --logo-grey: #6c6c6e;
  }
  * { margin: 0; padding: 0; box-sizing: border-box; }
  html, body {
    width: 1200px; height: 750px; overflow: hidden;
    background: var(--backdrop);
    font-family: "Play", sans-serif;
  }
  .stage { position: relative; width: 1200px; height: 750px; }
  .card {
    position: absolute; left: 371px; width: 461px; height: 262px;
    box-shadow: 0 3px 10px rgba(0,0,0,.5);
    overflow: hidden;
  }
  .card--front { top: 101px; background: var(--card-white); }
  .card--back {
    top: 401px;
    background: radial-gradient(ellipse at 48% 42%, #d6d6d7 0%, #bcbcbe 45%, #9c9c9e 100%);
  }
  .front-swoosh { position: absolute; inset: 0; }
  .holder-name {
    position: absolute; right: 16px; top: 23px;
    font-weight: 700; font-size: 17px; color: var(--ink);
  }
  .brand {
    position: absolute; left: 30px; top: 120px;
    display: flex; align-items: center; gap: 10px;
  }
  .brand__name {
    font-weight: 700; font-size: 30px; color: var(--logo-grey); letter-spacing: .5px;
  }
  .brand__dot {
    width: 22px; height: 22px; border-radius: 50%; background: var(--logo-grey);
  }
  .contact-list {
    position: absolute; left: 31px; top: 189px; list-style: none;
  }
  .contact-list li {
    display: flex; align-items: center; gap: 7px;
    height: 18px; font-size: 11px; color: var(--ink-soft);
  }
  .contact-list li.phone { font-size: 13px; }
  .contact-list svg { width: 12px; height: 12px; fill: var(--ink); flex: none; }
  .postal {
    position: absolute; left: 253px; top: 211px;
    font-size: 11.5px; line-height: 14px; color: var(--ink-soft);
  }
  .back-brand {
    position: absolute; left: 0; right: 0; top: 92px;
    display: flex; justify-content: center; align-items: center; gap: 12px;
  }
  .back-brand .brand__name { font-size: 34px; color: var(--ink); }
  .back-brand .brand__dot { width: 26px; height: 26px; background: var(--ink); }
  .back-url {
    position: absolute; left: 0; right: 0; top: 211px; text-align: center;
    font-size: 11px; font-style: italic; letter-spacing: 3px; color: var(--ink-soft);
  }
</style>
</head>
<body>
<div class="stage">
  <section class="card card--front">
    <svg class="front-swoosh" viewBox="0 0 461 262" preserveAspectRatio="none" aria-hidden="true">
      <defs>
        <linearGradient id="bandGrad" x1="0" y1="0" x2="1" y2="1">
          <stop offset="0" stop-color="#a9a9ab"/>
          <stop offset="1" stop-color="#8c8c8e"/>
        </linearGradient>
      </defs>
      <path d="M0 0 H461 V160 C420 90 330 50 170 38 C90 34 35 40 0 48 Z" fill="url(#bandGrad)"/>
      <path d="M0 48 C35 40 90 34 170 38 C330 50 420 90 461 160 V166 C420 100 330 60 170 46 C90 42 35 46 0 54 Z" fill="#d0d0d1"/>
      <path d="M0 54 C35 46 90 42 170 46 C330 60 420 100 461 166 V262 H0 Z" fill="#f7f7f7"/>
    </svg>
    <h1 class="holder-name">Morgan Kellaway</h1>
    <div class="brand">
      <span class="brand__name">Brisk Inquiries</span>
      <span class="brand__dot"></span>
    </div>
    <ul class="contact-list">
      <li class="phone">
        <svg viewBox="0 0 24 24"><path d="M6.6 10.8a15.1 15.1 0 0 0 6.6 6.6l2.2-2.2a1 1 0 0 1 1-.25 11.4 11.4 0 0 0 3.6.57 1 1 0 0 1 1 1V20a1 1 0 0 1-1 1A17 17 0 0 1 3 4a1 1 0 0 1 1-1h3.5a1 1 0 0 1 1 1c0 1.25.2 2.45.57 3.57a1 1 0 0 1-.25 1z"/></svg>
        0487 316 204
      </li>
      <li>
        <svg viewBox="0 0 24 24"><path d="M2 5h20v14H2z M3.5 6.5 12 13l8.5-6.5" fill="none" stroke="#2b2b2b" stroke-width="2"/></svg>
        info@briskinquiries-demo.com.au
      </li>
      <li>
        <svg viewBox="0 0 24 24"><circle cx="12" cy="12" r="10"/><path d="M2 12h20M12 2c3 3 3 17 0 20M12 2c-3 3-3 17 0 20" fill="none" stroke="#f7f7f7" stroke-width="1.5"/></svg>
        www.briskinquiries-demo.com.au
      </li>
    </ul>
    <address class="postal" style="font-style:normal">PO Box 58<br>Carnwell NSW 2291</address>
  </section>

  <section class="card card--back">
    <div class="back-brand">
      <span class="brand__name">Brisk Inquiries</span>
      <span class="brand__dot"></span>
    </div>
    <p class="back-url">www.briskinquiries-demo.com.au</p>
  </section>
</div>
</body>
</html>
```